Brintel Works - Fast, Efficient and Gas Mainteance for Domestic, Commercial and Industrial clients

We are in the process of purchasing a new business and would like to get a new logo and business card.
Business is a gas maintenance business that also does new gas installations.
Has been established since 1988.
Services include:
Install all types of gas appliances & equipment inc. hot water units
Maintain / repair / replace all types of gas appliances & equipment

Target Market(s)

Domestic, Commercial and Industrial clients

Industry/Entity Type

Business

Contact Information for Business Card

admin@brintelworks.com.au
07 3918 4726
Brintel Works PTY LTD

Logo Text

Gas Fitting & Plumbing Maintenance Specialists

Font styles to use
Sans Serif

Requirements
Must have
• Logo
• Business name, contact number, email address, web address
• Domestic | Commercial | Industrial Est Since 1988
Nice to have
• Possibly a black card with a flame logo to one side
Should not have
• Spelling errors

```html
<!DOCTYPE html>
<html lang="en">
<head>
<meta charset="utf-8">
<title>Brintel Works PTY LTD – Business Card</title>
<link rel="stylesheet" href="https://fonts.googleapis.com/css2?family=Open+Sans:wght@400;700&family=Great+Vibes&family=Tinos&display=swap">
<style>
  :root {
    --bg: #e9e6e1;
    --navy: #363e50;
    --navy-line: #2f3646;
    --red: #e0513a;
    --paper: #f1f1f1;
    --ink: #3b4252;
    --white: #ffffff;
    --muted: #5d6474;
  }
  * { margin: 0; padding: 0; box-sizing: border-box; }
  html, body { width: 1200px; height: 902px; overflow: hidden; }
  body {
    background: var(--bg);
    font-family: "Open Sans", sans-serif;
    position: relative;
  }
  .card {
    position: absolute;
    left: 250px;
    width: 700px;
    height: 400px;
    border-radius: 6px;
    overflow: hidden;
    box-shadow: 0 6px 18px rgba(0,0,0,0.18);
  }
  .card--front { top: 27px; background: var(--paper); }
  .card--back  { top: 475px; background: var(--navy); }

  .card__shapes { position: absolute; inset: 0; }

  .brand {
    position: absolute;
    left: 0; right: 0;
    text-align: center;
  }
  .brand__name {
    font-weight: 700;
    color: var(--red);
    letter-spacing: 1px;
    display: inline-block;
    position: relative;
  }
  .brand__suffix {
    position: absolute;
    left: 100%;
    top: 4px;
    margin-left: 6px;
    font-size: 9px;
    font-weight: 700;
    letter-spacing: 0.5px;
    white-space: nowrap;
  }
  .brand__tagline {
    font-weight: 700;
    display: block;
  }

  /* Front */
  .card--front .brand { top: 34px; }
  .card--front .brand__name { font-size: 44px; }
  .card--front .brand__suffix { color: var(--ink); }
  .card--front .brand__tagline { font-size: 25px; color: var(--ink); margin-top: -4px; }
  .sectors {
    position: absolute;
    top: 146px; left: 0; right: 0;
    text-align: center;
    font-size: 14px;
    color: var(--muted);
  }
  .sectors__est {
    font-family: "Great Vibes", cursive;
    font-size: 26px;
    color: var(--ink);
    margin-left: 12px;
    vertical-align: -3px;
  }
  .contact {
    position: absolute;
    top: 262px; left: 0; right: 0;
    text-align: center;
    font-family: "Tinos", serif;
    font-size: 21px;
    line-height: 31px;
    color: var(--white);
    list-style: none;
  }

  /* Back */
  .card--back .brand { top: 130px; }
  .card--back .brand__name { font-size: 58px; }
  .card--back .brand__suffix { color: var(--white); font-size: 11px; }
  .card--back .brand__tagline { font-size: 32px; color: var(--white); margin-top: -6px; }
</style>
</head>
<body>

<section class="card card--front" aria-label="Card front">
  <svg class="card__shapes" width="700" height="400" viewBox="0 0 700 400" aria-hidden="true">
    <polygon points="0,250 40,236 620,236 700,60 700,400 0,400" fill="var(--red)"/>
    <polygon points="0,250 40,236 620,236 700,60 700,44 612,226 34,226 0,238" fill="var(--navy-line)"/>
  </svg>
  <div class="brand">
    <span class="brand__name">BRINTEL WORKS<span class="brand__suffix">PTY LTD</span></span>
    <span class="brand__tagline">Gas fitting &amp; Plumbing Specialists</span>
  </div>
  <p class="sectors">Domestic | Commercial | Industrial <span class="sectors__est">Est Since 1988</span></p>
  <ul class="contact">
    <li>07 3918 4726</li>
    <li>admin@brintelworks.com.au</li>
    <li>www.brintelworks.com.au</li>
    <li>PO Box 2854, Coorparoo, QLD 4151</li>
  </ul>
</section>

<section class="card card--back" aria-label="Card back">
  <div class="brand">
    <span class="brand__name">BRINTEL WORKS<span class="brand__suffix">PTY LTD</span></span>
    <span class="brand__tagline">Gas fitting &amp; Plumbing Specialists</span>
  </div>
</section>

</body>
</html>
```